Business card design for new eCommerce site focusing on integrity and strong businsess tactics

We need a business card that will stand out and be memorable. Something with color that matches our company logo colors. Think high end version of Pactivo. There are 2 logos provided. The parent company is called Amber Ledge Partners and we are presenting a new and very exciting eCommerce site called BrightHarborTrade.example.

Target Market(s)

Our target markets are in the Activities, Food and Beverage, Health and Beauty

Industry/Entity Type

Marketing

Contact Information for Business Card

We have 4 members that need cards...I will provide all info to the winner of the design contest
Business Address is
4870 West 63rd Avenue, Suite C207
Phoenix AZ 85731

Font styles to use
Serif
Sans Serif

Colors

Designer to choose colors to be used in the design.

Requirements
Must have
• The card must be memorable...should be unique in design but must exude integrity and be playful .
• I have provided several colors or our parent company...please feel free to use which ever
Nice to have
• I will leave this up to you. Feel free to use other images of your choosing that wraps around our client.....Activities, Dining, Health, Beauty
Should not have
• just dont be boring

```html
<!DOCTYPE html>
<html lang="en">
<head>
<meta charset="utf-8">
<title>BrightHarborTrade.example business card</title>
<link href="https://fonts.googleapis.com/css2?family=Questrial&family=Arimo:wght@700&family=PT+Sans+Narrow:wght@700&display=swap" rel="stylesheet">
<style>
  :root {
    --backdrop: #2c2c2c;
    --card-white: #f3f3f3;
    --brand-blue: #2a78a8;
    --brand-green: #79b829;
    --text-grey: #555555;
    --white: #ffffff;
  }
  html, body {
    margin: 0;
    padding: 0;
    width: 1200px;
    height: 960px;
    overflow: hidden;
    background: var(--backdrop);
  }
  .canvas {
    position: relative;
    width: 1200px;
    height: 960px;
    font-family: "Questrial", sans-serif;
  }
  .card {
    position: absolute;
    width: 600px;
    height: 343px;
    box-shadow: 0 2px 6px rgba(0,0,0,0.5);
    overflow: hidden;
  }
  .card-front { left: 314px; top: 113px; background: var(--card-white); }
  .card-back  { left: 311px; top: 472px; background: var(--brand-blue); }

  .brand-mark {
    position: absolute;
    left: 44px;
    top: 52px;
    width: 58px;
    height: 58px;
    border-radius: 50%;
    background: var(--brand-blue);
  }
  .brand-name {
    position: absolute;
    left: 116px;
    top: 66px;
    margin: 0;
    font-size: 25px;
    color: var(--brand-green);
    font-weight: 400;
    letter-spacing: -0.3px;
  }
  .brand-tagline {
    position: absolute;
    left: 117px;
    top: 98px;
    margin: 0;
    font-size: 13px;
    color: var(--text-grey);
    letter-spacing: 0.6px;
  }
  .address {
    position: absolute;
    left: 48px;
    top: 173px;
    margin: 0;
    font-size: 15px;
    line-height: 18px;
    color: var(--text-grey);
    font-style: normal;
  }
  .contact-list {
    position: absolute;
    left: 48px;
    top: 217px;
    margin: 0;
    padding: 0;
    list-style: none;
    font-size: 14.5px;
    color: var(--text-grey);
  }
  .contact-list li {
    display: flex;
    align-items: center;
    height: 19.5px;
  }
  .contact-list svg {
    width: 14px;
    height: 14px;
    margin-right: 8px;
    fill: var(--brand-blue);
  }
  .person {
    position: absolute;
    right: 37px;
    top: 202px;
    text-align: right;
  }
  .person-name {
    margin: 0;
    font-family: "PT Sans Narrow", sans-serif;
    font-weight: 700;
    font-size: 22px;
    color: var(--brand-blue);
    letter-spacing: 0.3px;
  }
  .person-role {
    margin: 0;
    font-size: 15px;
    color: var(--brand-green);
  }
  .footer-band {
    position: absolute;
    left: 0;
    bottom: 0;
    width: 600px;
    height: 30px;
  }
  .website {
    position: absolute;
    left: 48px;
    bottom: 7px;
    margin: 0;
    font-size: 14px;
    color: var(--white);
  }

  .back-ring {
    position: absolute;
    left: 228px;
    top: 71px;
    width: 142px;
    height: 142px;
    border: 3px solid var(--white);
    border-radius: 50%;
    box-sizing: border-box;
  }
  .back-name {
    position: absolute;
    left: 0;
    width: 600px;
    top: 222px;
    margin: 0;
    text-align: center;
    font-family: "Arimo", sans-serif;
    font-weight: 700;
    font-size: 32px;
    color: var(--white);
  }
</style>
</head>
<body>
<div class="canvas">
  <section class="card card-front">
    <span class="brand-mark"></span>
    <h1 class="brand-name">BrightHarborTrade.example</h1>
    <p class="brand-tagline">Activities-Dining-Health-Beauty</p>

    <address class="address">4870 West 63rd Avenue<br>Suite C207, Phoenix AZ 85731</address>

    <ul class="contact-list">
      <li>
        <svg viewBox="0 0 16 16"><path d="M3.6 1.2l2.3 2.3c.4.4.4 1 0 1.4L4.7 6.1c.9 2 2.4 3.5 4.4 4.4l1.2-1.2c.4-.4 1-.4 1.4 0l2.3 2.3c.4.4.4 1 0 1.4l-1.3 1.3c-.7.7-1.8.9-2.7.4C6.6 13.2 3.2 9.8 1.8 6.4c-.4-.9-.2-2 .4-2.7L3.5 2.4"/></svg>
        602 555 0148
      </li>
      <li>
        <svg viewBox="0 0 16 16"><path d="M4.5 1h7c.6 0 1 .4 1 1v12c0 .6-.4 1-1 1h-7c-.6 0-1-.4-1-1V2c0-.6.4-1 1-1zm.8 2v9h5.4V3H5.3zM8 12.6a.8.8 0 100 1.6.8.8 0 000-1.6z"/></svg>
        602 555 0193
      </li>
      <li>
        <svg viewBox="0 0 16 16"><path d="M1 3.5h14v9H1v-9zm1.4 1.2L8 8.6l5.6-3.9H2.4zm-.2 1.4v5.2h11.6V6.1L8 10.1 2.2 6.1z"/></svg>
        dana@brightharbortrade.example
      </li>
    </ul>

    <div class="person">
      <p class="person-name">DANA WHITLOW</p>
      <p class="person-role">CEO/FOUNDER</p>
    </div>

    <svg class="footer-band" viewBox="0 0 600 30" preserveAspectRatio="none">
      <rect x="0" y="0" width="470" height="30" fill="var(--brand-blue)"/>
      <polygon points="488,30 508,0 600,0 600,30" fill="var(--brand-green)"/>
    </svg>
    <p class="website">www.brightharbortrade.example</p>
  </section>

  <section class="card card-back">
    <span class="back-ring"></span>
    <h2 class="back-name">Amber Ledge Partners</h2>
  </section>
</div>
</body>
</html>
```